Velmora Consulting Business

** Please add the content information from my old business card
1. I would like to see a two sided business card with both options with the 1st Option--Tallow Spire-new WHITE BACKGROUND LOGO
2 nd Option-Tallow Spire - new BLACK- Background Logo
3rd -Option a business card with my Photo on the card
Please add the new word to the card information:
EXECUTION
AS THE OWNER'S REP
WE AIM TO ACHIEVE YOUR
INFRASTRUCTURE VISION with
OUR SPECIALIZATION & EXECUTION in:

FUNDING Planning
BUSINESS Planning
INFRASTRUCTURE Planning
PROJECT Management
Since 2012
_____________________________________________________________________
I want to get spot uv raised printing. I was liking a a nice rich white linen paper stock with black writing & NOT A COLORED CARD other than a variety of white or black cards concept

```html
<!DOCTYPE html>
<html lang="en">
<head>
<meta charset="utf-8">
<title>Velmora Consulting – Business Card</title>
<link href="https://fonts.googleapis.com/css2?family=Montserrat:wght@400;500;700&family=Tinos&display=swap" rel="stylesheet">
<style>
  :root {
    --stage: #262626;
    --paper: #ffffff;
    --ink: #231f20;
    --ink-soft: #333333;
    --brand-red: #e31b3a;
    --card-black: #000000;
    --on-black: #f2f2f2;
    --whisper: #1c1c1c;
  }
  * { box-sizing: border-box; margin: 0; padding: 0; }
  html, body { width: 1200px; height: 1059px; overflow: hidden; }
  body {
    background: var(--stage);
    font-family: "Montserrat", Arial, sans-serif;
    position: relative;
  }
  .card { position: absolute; border-radius: 22px; overflow: hidden; }

  /* Front */
  .card-front { left: 256px; top: 98px; width: 689px; height: 382px; background: var(--paper); }
  .wordmark {
    position: absolute; left: 0; right: 0; top: 110px;
    text-align: center; font-weight: 700; font-size: 40px; color: var(--ink); letter-spacing: -0.5px;
  }
  .person { position: absolute; right: 355px; top: 220px; text-align: right; white-space: nowrap; }
  .person-name { font-weight: 700; font-size: 21px; color: var(--brand-red); }
  .person-role { font-weight: 500; font-size: 12px; color: var(--ink-soft); margin-top: 4px; letter-spacing: 0.2px; }
  .front-divider { position: absolute; left: 351px; top: 214px; width: 1.5px; height: 62px; background: var(--brand-red); }
  .contact-list { position: absolute; left: 365px; top: 212px; list-style: none; }
  .contact-list li { display: flex; align-items: center; height: 21px; font-size: 14px; color: var(--ink); }
  .contact-list svg { width: 15px; height: 15px; margin-right: 14px; fill: var(--brand-red); }
  .office-band {
    position: absolute; left: 0; right: 0; top: 312px; height: 47px;
    background: var(--brand-red); color: #fff; font-size: 14px;
    display: flex; align-items: center; justify-content: center; letter-spacing: 0.3px;
  }

  /* Back */
  .card-back { left: 252px; top: 546px; width: 709px; height: 394px; background: var(--card-black); }
  .wordmark-reverse {
    position: absolute; left: 40px; width: 310px; top: 185px;
    text-align: center; font-weight: 700; font-size: 34px; color: var(--on-black); letter-spacing: -0.5px;
  }
  .back-divider { position: absolute; left: 338px; top: 105px; width: 1px; height: 213px; background: #7a1222; }
  .mission {
    position: absolute; left: 359px; top: 106px;
    font-family: "Tinos", "Times New Roman", serif; font-size: 15px; line-height: 19.4px;
    color: var(--brand-red); text-transform: none;
  }
  .mission strong { font-family: "Montserrat", Arial, sans-serif; font-weight: 700; font-size: 14px; }
  .service-list { position: absolute; left: 359px; top: 208px; list-style: none; }
  .service-list li { display: flex; align-items: center; height: 30.2px; font-size: 15px; color: var(--on-black); letter-spacing: 0.3px; }
  .service-list .bullet { width: 9px; height: 9px; background: var(--brand-red); transform: rotate(45deg); margin: 0 19px 0 4px; }
  .since { position: absolute; left: 539px; top: 360px; font-size: 14px; color: var(--whisper); }
</style>
</head>
<body>

<section class="card card-front" aria-label="Business card front">
  <div class="wordmark">Velmora Consulting</div>

  <div class="person">
    <div class="person-name">Renata Halvorsen-Dube</div>
    <div class="person-role">CEO / LEAD PROJECT MANAGER</div>
  </div>

  <div class="front-divider"></div>

  <ul class="contact-list">
    <li>
      <svg viewBox="0 0 16 16" aria-hidden="true"><path d="M1 6c0-2 3-3 7-3s7 1 7 3v1h-3V5.5C11 5 9.5 4.8 8 4.8S5 5 4 5.5V7H1z M3.5 8h9l1.5 5H2z"/></svg>
      867.555.0142
    </li>
    <li>
      <svg viewBox="0 0 16 16" aria-hidden="true"><path d="M1 3h14v1.5L8 9 1 4.5z M1 6.2l7 4.5 7-4.5V13H1z"/></svg>
      renata@velmora.ca
    </li>
    <li>
      <svg viewBox="0 0 16 16" aria-hidden="true"><circle cx="8" cy="8" r="7"/><path d="M4 4.5c1.5 0 2.5 1 2 2.5S7.5 9 6.5 11" stroke="#fff" stroke-width="1.2" fill="none"/><path d="M10 3c.5 2 2.5 2 3 4" stroke="#fff" stroke-width="1.2" fill="none"/></svg>
      www.velmora.ca
    </li>
  </ul>

  <div class="office-band">Northgate NT · Alderbrook NB</div>
</section>

<section class="card card-back" aria-label="Business card back">
  <div class="wordmark-reverse">Velmora Consulting</div>

  <div class="back-divider"></div>

  <p class="mission">
    AS THE <strong>OWNER'S REP</strong><br>
    WE AIM TO ACHIEVE YOUR<br>
    INFRASTRUCTURE VISION with<br>
    OUR SPECIALIZATION in:
  </p>

  <ul class="service-list">
    <li><span class="bullet"></span>FUNDING Planning</li>
    <li><span class="bullet"></span>BUSINESS Planning</li>
    <li><span class="bullet"></span>INFRASTRUCTURE Planning</li>
    <li><span class="bullet"></span>PROJECT Management</li>
  </ul>

  <div class="since">Since 2012</div>
</section>

</body>
</html>
```